Advertising company unique advertising platform

we need a logo design for a new company based in Australia Melbourne. We develop innovated advertising platform where consumer can use this platform to get regular discount, as business owner they can use this platform for free advertisement. Payment for this advertisement platform only payable every two weeks, when I generate revenue for their business

Industry/Entity Type

Advertising

Contact Information for Business Card

Dale Morven | Co-Founder |Managing Director
Suite 718 240 Wattlebrook Lane Melbourne Vic 3000

ABN 38 614 207 923
Tel: +61 0487 259 318 | Email: dale.morven@plivorantu.com

Font styles to use
Decorative
Script

Requirements
Must have
• Try few different design and some round corner business card
Should not have
• One round corner business card...try 4 different colour background not only black, make sure two side is designed. Be creative so imagine you are giving this to a client make sure has wow factor, if you can also try one design with engrave like all the logo, words look 3d feel
• The word Advertising Platform use attached file font

```html
<!DOCTYPE html>
<html lang="en">
<head>
<meta charset="utf-8">
<title>Tallowmere Exchange — Business Card</title>
<link rel="stylesheet" href="https://fonts.googleapis.com/css2?family=Marcellus&family=Work+Sans:wght@400;500&display=swap">
<style>
  :root {
    --page-bg: #e9e6e1;
    --card-dark: #2b2b2c;
    --card-dark-edge: #202021;
    --card-light: #ffffff;
    --accent: #f08a2c;
    --ink: #2a2a2a;
    --ink-soft: #6b6b6b;
  }
  * { box-sizing: border-box; margin: 0; padding: 0; }
  html, body {
    width: 1200px; height: 900px; overflow: hidden;
    background: var(--page-bg);
  }
  .sheet {
    width: 1200px; height: 900px;
    display: flex; flex-direction: column;
    align-items: center; justify-content: center; gap: 56px;
  }
  .card {
    width: 630px; height: 360px;
    border-radius: 26px;
    position: relative;
    box-shadow: 0 10px 28px rgba(0,0,0,.18);
  }
  /* Front */
  .card--front {
    background: radial-gradient(ellipse at 55% 40%, #3a3a3b 0%, var(--card-dark) 55%, var(--card-dark-edge) 100%);
    display: flex; align-items: center; justify-content: center; gap: 16px;
  }
  .brand-dot {
    width: 22px; height: 22px; border-radius: 50%;
    background: var(--accent);
  }
  .brand-name {
    font-family: "Marcellus", serif;
    font-size: 40px; letter-spacing: 1px;
    color: var(--accent);
  }
  /* Back */
  .card--back {
    background: var(--card-light);
  }
  .back-brand {
    position: absolute; left: 34px; top: 160px; width: 200px;
    display: flex; flex-direction: column; align-items: center; gap: 12px;
  }
  .back-brand .brand-name { font-size: 24px; text-align: center; line-height: 1.2; }
  .divider {
    position: absolute; left: 262px; top: 92px;
    width: 2px; height: 178px; background: var(--accent);
  }
  .details {
    position: absolute; left: 300px; top: 82px;
  }
  .person-name {
    font-family: "Marcellus", serif;
    font-size: 30px; color: var(--accent);
    letter-spacing: 1px; text-transform: uppercase; line-height: 1;
  }
  .person-role {
    font-family: "Marcellus", serif;
    font-size: 12.5px; color: var(--ink-soft);
    text-transform: uppercase; margin-top: 6px; letter-spacing: .3px;
  }
  .contact {
    list-style: none; margin-top: 20px;
    font-family: "Work Sans", sans-serif; font-size: 16px;
    color: var(--ink); line-height: 1.42;
  }
  .contact .label { color: var(--accent); }
  .contact .icon {
    display: inline-block; width: 14px; height: 14px;
    vertical-align: -2px; margin-right: 8px;
  }
  .contact .icon path, .contact .icon rect { stroke: var(--accent); fill: none; stroke-width: 1.6; }
</style>
</head>
<body>
<main class="sheet">
  <section class="card card--front" aria-label="Card front">
    <span class="brand-dot"></span>
    <span class="brand-name">Tallowmere Exchange</span>
  </section>

  <section class="card card--back" aria-label="Card back">
    <div class="back-brand">
      <span class="brand-dot"></span>
      <span class="brand-name">Tallowmere Exchange</span>
    </div>
    <div class="divider"></div>
    <div class="details">
      <h1 class="person-name">Dale Morven</h1>
      <p class="person-role">|Co-Founder | Managing Director</p>
      <ul class="contact">
        <li>Suite 718 240 Wattlebrook Lane</li>
        <li>Melbourne Vic 3000</li>
        <li><span class="label">ABN:</span> 38 614 207 923</li>
        <li>
          <svg class="icon" viewBox="0 0 14 14" aria-hidden="true"><path d="M3 1.5l2.2 2.6-1.3 1.6c.9 1.8 2.3 3.2 4.1 4.1l1.6-1.3 2.6 2.2-1.4 1.8C6 12.4 1.6 8 1.3 2.9z"/></svg>+61 0487 259 318
        </li>
        <li>
          <svg class="icon" viewBox="0 0 14 14" aria-hidden="true"><rect x="1" y="3" width="12" height="8.5" rx="1"/><path d="M1.3 3.4L7 8l5.7-4.6"/></svg>dale.morven@plivorantu.com
        </li>
      </ul>
    </div>
  </section>
</main>
</body>
</html>
```